Unique Business Card Design

Unique Business Card design for our orthotic and prosthetic company. Our logo is on our website, color is light blue. Unique shape (artificial leg shaped, vertical, etc..) preferred. Logo, business name, individual name and basic demographics needed.

Industry/Entity Type

Business

Contact Information for Business Card

Logo, Industry, Phone # Logo, "Prosthetic & Orthotic Services" Place to add individual name and contact info

Colors
cee9f5

Requirements
Must have
• The icon must be there, placement of "Prosthetic & Orthotic Services" can be moved
Nice to have
• Like the mix of light blue, and a little darker blue. One design included the icons from my website which was a nice touch

```html
<!DOCTYPE html>
<html lang="en">
<head>
<meta charset="utf-8">
<title>Limbwell Inc. Business Card</title>
<link rel="stylesheet" href="https://fonts.googleapis.com/css2?family=Open+Sans:ital,wght@0,400;0,600;0,700;1,400&display=swap">
<style>
  :root {
    --backdrop: #3d3d3d;
    --paper: #ffffff;
    --brand-blue: #1560ac;
    --card-blue: #1a5fad;
    --faint-blue: #3f7cc0;
    --ink: #555555;
    --ink-strong: #444444;
    --white: #ffffff;
  }
  * { box-sizing: border-box; margin: 0; padding: 0; }
  html, body {
    width: 1105px; height: 1200px; overflow: hidden;
    background: var(--backdrop);
    font-family: "Open Sans", Arial, sans-serif;
  }
  .canvas { position: relative; width: 1105px; height: 1200px; }
  .card {
    position: absolute; left: 193px; width: 721px; height: 409px; overflow: hidden;
  }
  .card-front { top: 168px; background: var(--paper); }
  .card-back { top: 624px; background: var(--card-blue); }

  .brand-mark {
    position: absolute; left: 280px; top: 58px; width: 102px; height: 102px;
    border-radius: 50%; background: var(--brand-blue);
  }
  .brand-name {
    position: absolute; left: 412px; top: 72px;
    font-size: 30px; font-weight: 700; color: var(--brand-blue); letter-spacing: -0.5px;
  }
  .brand-tagline {
    position: absolute; left: 426px; top: 112px;
    font-size: 16px; color: var(--brand-blue);
  }

  .person { position: absolute; left: 37px; top: 258px; }
  .person-name { font-size: 26px; font-weight: 600; color: var(--brand-blue); line-height: 34px; }
  .person-title { font-size: 18px; font-weight: 600; color: var(--brand-blue); line-height: 24px; }
  .person-line { font-size: 18px; color: var(--ink); line-height: 28px; }
  .person-email { font-style: italic; }
  .label { font-weight: 700; color: var(--ink-strong); }

  .company-contact {
    position: absolute; right: 36px; top: 264px; text-align: right;
    font-size: 18px; color: var(--ink); line-height: 28.5px;
  }
  .company-web { font-weight: 700; color: var(--brand-blue); }

  .back-decoration {
    position: absolute; left: 14px; top: 4px; width: 400px; height: 400px;
    border-radius: 50%; background: var(--faint-blue); opacity: 0.55;
  }
  .back-name {
    position: absolute; right: 30px; top: 292px;
    font-size: 33px; font-weight: 700; color: var(--white); letter-spacing: -0.5px;
  }
  .back-tagline {
    position: absolute; right: 42px; top: 348px;
    font-size: 17px; color: var(--white);
  }
</style>
</head>
<body>
<main class="canvas">
  <section class="card card-front">
    <div class="brand-mark"></div>
    <div class="brand-name">LIMBWELL INC.</div>
    <div class="brand-tagline">Prosthetic &amp; Orthotic Services</div>

    <div class="person">
      <div class="person-name">MIRIAM HALLORAN</div>
      <div class="person-title">CO LPO</div>
      <div class="person-line"><span class="label">Cell:</span> 555.204.7731</div>
      <div class="person-line person-email">mhalloran@limbwellinc.com</div>
    </div>

    <div class="company-contact">
      <div><span class="label">Tel:</span> 555.204.1600</div>
      <div><span class="label">Fax:</span> 555-2048820</div>
      <div>2210 W. 14th St., Fairview, NY 10990</div>
      <div class="company-web">www.limbwellinc.com</div>
    </div>
  </section>

  <section class="card card-back">
    <div class="back-decoration"></div>
    <div class="back-name">LIMBWELL INC.</div>
    <div class="back-tagline">Prosthetic &amp; Orthotic Services</div>
  </section>
</main>
</body>
</html>
```